New Business Card Design Project

Use the flyer uploaded and website www.brightoakbuilders.com for inspiration.
List Our Services on Backside of business cards
Marcus Delling
Harborline Builders Inc.
Licensed General Contractors
858-471-6093

Contact Information for Business Card

Use the flyer uploaded and website www.brightoakbuilders.com for inspiration. List Our Services on Backside of business cards Marcus Delling Harborline Builders Inc. Licensed General Contractors 858-471-6093

```html
<!DOCTYPE html>
<html lang="en">
<head>
<meta charset="utf-8">
<title>Harborline Builders – Business Card</title>
<link rel="stylesheet" href="https://fonts.googleapis.com/css2?family=Cinzel:wght@400;600&family=Montserrat:wght@400;500&display=swap">
<style>
  :root {
    --backdrop: #2b2b2c;
    --card: #19191a;
    --card-edge: #232325;
    --ink: #f4f4f4;
    --ink-soft: #dcdcdc;
  }
  * { margin: 0; padding: 0; box-sizing: border-box; }
  html, body { width: 1200px; height: 900px; overflow: hidden; }
  body {
    background: var(--backdrop);
    font-family: "Montserrat", sans-serif;
    color: var(--ink);
    position: relative;
  }
  .card {
    position: absolute;
    left: 280px;
    width: 640px;
    height: 366px;
    border-radius: 14px;
    background: linear-gradient(135deg, var(--card) 0%, var(--card-edge) 100%);
    box-shadow: 0 10px 24px rgba(0,0,0,0.45);
    overflow: hidden;
  }
  .card--front { top: 50px; }
  .card--back { top: 480px; }

  .wordmark {
    font-family: "Cinzel", serif;
    font-weight: 400;
    color: var(--ink);
    letter-spacing: 0.04em;
    white-space: nowrap;
  }

  /* Front */
  .front-wordmark {
    position: absolute;
    top: 160px; left: 0; right: 0;
    text-align: center;
    font-size: 34px;
    line-height: 46px;
  }

  /* Back */
  .back-content {
    position: absolute;
    left: 48px; top: 40px;
  }
  .back-wordmark { font-size: 26px; line-height: 34px; }
  .person-name {
    font-family: "Cinzel", serif;
    font-weight: 600;
    font-size: 25px;
    margin-top: 40px;
    letter-spacing: 0.03em;
  }
  .person-title {
    font-size: 15px;
    color: var(--ink-soft);
    margin-top: 2px;
  }
  .contact-list {
    list-style: none;
    margin-top: 20px;
  }
  .contact-item {
    display: flex;
    align-items: center;
    gap: 10px;
    font-size: 16px;
    margin-bottom: 6px;
    color: var(--ink);
  }
  .contact-icon { width: 15px; height: 15px; flex: none; }
  .company-name {
    font-size: 16px;
    margin-top: 18px;
    color: var(--ink);
  }
</style>
</head>
<body>
  <section class="card card--front" aria-label="Card front">
    <div class="wordmark front-wordmark">Harborline Builders</div>
  </section>

  <section class="card card--back" aria-label="Card back">
    <div class="back-content">
      <div class="wordmark back-wordmark">Harborline Builders</div>
      <div class="person-name">Marcus Delling</div>
      <div class="person-title">Licensed General Contractors</div>
      <ul class="contact-list">
        <li class="contact-item">
          <svg class="contact-icon" viewBox="0 0 24 24" fill="var(--ink)"><path d="M6.6 10.8a15.1 15.1 0 0 0 6.6 6.6l2.2-2.2a1 1 0 0 1 1-.25 11.4 11.4 0 0 0 3.6.57 1 1 0 0 1 1 1V20a1 1 0 0 1-1 1A17 17 0 0 1 3 4a1 1 0 0 1 1-1h3.5a1 1 0 0 1 1 1c0 1.25.2 2.46.57 3.6a1 1 0 0 1-.25 1z"/></svg>
          858-471-6093
        </li>
        <li class="contact-item">
          <svg class="contact-icon" viewBox="0 0 24 24" fill="var(--ink)"><path d="M3 5h18a1 1 0 0 1 1 1v12a1 1 0 0 1-1 1H3a1 1 0 0 1-1-1V6a1 1 0 0 1 1-1zm0 2v.4l9 5.6 9-5.6V7l-9 5.6z"/></svg>
          info@brightoakbuilders.com
        </li>
        <li class="contact-item">
          <svg class="contact-icon" viewBox="0 0 24 24" fill="none" stroke="var(--ink)" stroke-width="2"><circle cx="12" cy="12" r="9"/><path d="M3 12h18M12 3c3 3 3 15 0 18M12 3c-3 3-3 15 0 18"/></svg>
          www.brightoakbuilders.com
        </li>
      </ul>
      <div class="company-name">Harborline Builders Inc.</div>
    </div>
  </section>
</body>
</html>
```